design a construction company business card

Design business card around our logo. Card must have all the typical info: name, title, address, phone, email, business name, etc. Somewhere on the card I would like to see our motto "Built on integrity... Inspired by commitment." Consider adding a splash of bright orange to the card to complement the blues and silvers/grays in the logo. We are open to metallic inks, textures, etc. We would like to see options on both light and dark backgrounds. The font in the logo is Euro Technic Extended Regular.

```html
<!DOCTYPE html>
<html lang="en">
<head>
<meta charset="utf-8">
<title>Halden Contracting business cards</title>
<link href="https://fonts.googleapis.com/css2?family=Open+Sans:wght@400;600;700&display=swap" rel="stylesheet">
<style>
  :root{
    --backdrop:#e4e5e8;
    --card:#ffffff;
    --brand-blue:#2a4fb8;
    --blue-deep:#233c9e;
    --blue-bright:#1f7fd0;
    --ink-grey:#555a61;
    --white:#ffffff;
  }
  *{margin:0;padding:0;box-sizing:border-box}
  html,body{width:1200px;height:892px;overflow:hidden}
  body{background:var(--backdrop);font-family:"Open Sans",Arial,sans-serif;position:relative}
  .card{position:absolute;background:var(--card);box-shadow:0 10px 30px rgba(0,0,0,.18)}

  .card-front{left:110px;top:286px;width:560px;height:320px}
  .front-brand{position:absolute;left:0;right:0;top:96px;display:flex;align-items:center;justify-content:center;gap:14px}
  .brand-square{display:block;width:30px;height:30px;background:var(--brand-blue);flex:none}
  .front-name{font-weight:700;font-size:27px;letter-spacing:2px;color:var(--brand-blue);line-height:32px}
  .motto{position:absolute;left:0;right:0;top:226px;text-align:center;font-size:15px;color:var(--ink-grey)}

  .card-back{left:770px;top:166px;width:320px;height:560px;overflow:hidden}
  .back-brand{position:absolute;left:0;right:0;top:96px;display:flex;flex-direction:column;align-items:center;gap:22px}
  .back-square{width:64px;height:64px}
  .back-name{text-align:center;font-weight:700;font-size:24px;line-height:32px;letter-spacing:2px;color:var(--brand-blue)}
  .blue-panel{position:absolute;left:0;top:0;width:320px;height:560px}
  .contact{position:absolute;left:0;right:0;top:372px;text-align:center;color:var(--white);font-size:14px;line-height:20px}
  .person{font-weight:700;font-size:21px;letter-spacing:1px;line-height:26px}
  .role{font-size:13px;letter-spacing:1px;margin-bottom:14px}
  .address{margin-bottom:10px}
  .label{font-weight:700}
</style>
</head>
<body>
  <section class="card card-front">
    <div class="front-brand">
      <span class="brand-square"></span>
      <div class="front-name">HALDEN CONTRACTING, INC.</div>
    </div>
    <p class="motto">Built on integrity... Inspired by commitment.</p>
  </section>

  <section class="card card-back">
    <div class="back-brand">
      <span class="brand-square back-square"></span>
      <div class="back-name">HALDEN<br>CONTRACTING, INC.</div>
    </div>
    <svg class="blue-panel" viewBox="0 0 320 560" aria-hidden="true">
      <defs>
        <radialGradient id="panelGlow" cx="50%" cy="55%" r="70%">
          <stop offset="0" stop-color="#1f7fd0"/>
          <stop offset="1" stop-color="#233c9e"/>
        </radialGradient>
      </defs>
      <polygon points="0,348 320,330 320,560 0,560" fill="url(#panelGlow)"/>
      <line x1="0" y1="348" x2="320" y2="330" stroke="#233c9e" stroke-width="3"/>
    </svg>
    <div class="contact">
      <div class="person">MARCUS HALE</div>
      <div class="role">PRESIDENT</div>
      <div class="address">2170 Larkspur Avenue<br>Cedar Grove, NY 11530</div>
      <div><span class="label">P:</span> 555 0143 2287 <span class="label">E:</span> marcus@halden.com</div>
      <div><span class="label">W:</span> www.halden.com</div>
    </div>
  </section>
</body>
</html>
```